Company director needs a business card design

I am a semi-retired former senior finance executive who sits on a number of public and private company boards and do some consulting work. I work largely with emerging businesses but deal regularly with top end of town lawyers, bankers etc. I need a thoughtful but relatively conservative design which would also resonate with my younger client base. Some colour would be good. Information limited to name, address, office tel, mobile and email.

Finance

```html
<!DOCTYPE html>
<html lang="en">
<head>
<meta charset="UTF-8">
<title>Business Card</title>
<link rel="stylesheet" href="https://fonts.googleapis.com/css2?family=Cinzel:wght@400&family=Crimson+Pro:wght@400;500&display=swap">
<style>
  :root {
    --backdrop: #e6e6e8;
    --teal: #1ca6a8;
    --paper: #ffffff;
    --ink: #151515;
    --name-ink: #ffffff;
  }
  html, body {
    margin: 0;
    padding: 0;
    width: 1200px;
    height: 864px;
    overflow: hidden;
    background: var(--backdrop);
  }
  .stage {
    width: 1200px;
    height: 864px;
    display: flex;
    align-items: center;
    justify-content: center;
  }
  .card {
    width: 910px;
    height: 520px;
    display: flex;
    background: var(--paper);
    box-shadow: 0 18px 40px rgba(0,0,0,0.18);
  }
  .card__identity {
    width: 44%;
    background: var(--teal);
    display: flex;
    align-items: center;
    justify-content: center;
  }
  .card__name {
    margin: 0;
    font-family: "Cinzel", serif;
    font-weight: 400;
    font-size: 38px;
    letter-spacing: 1px;
    color: var(--name-ink);
  }
  .card__contact {
    flex: 1;
    display: flex;
    flex-direction: column;
    justify-content: center;
    padding: 60px 20px 40px 40px;
  }
  .contact-list {
    list-style: none;
    margin: 0;
    padding: 0;
    font-family: "Crimson Pro", serif;
    font-size: 28px;
    line-height: 1.2;
    color: var(--ink);
  }
  .contact-item {
    display: flex;
    align-items: flex-start;
    margin-bottom: 14px;
  }
  .contact-item__icon {
    width: 24px;
    height: 24px;
    flex: none;
    margin-right: 44px;
    margin-top: 8px;
    fill: var(--ink);
  }
  .contact-item--email .contact-item__text {
    font-weight: 500;
  }
</style>
</head>
<body>
<main class="stage">
  <article class="card">
    <section class="card__identity">
      <h1 class="card__name">Your Name</h1>
    </section>
    <section class="card__contact">
      <ul class="contact-list">
        <li class="contact-item">
          <svg class="contact-item__icon" viewBox="0 0 24 24" aria-hidden="true"><path d="M6.6 2.5l3 3.6-1.8 2.2c1.1 2.7 3.2 4.9 5.9 6.1l2.2-1.8 3.6 3-1.9 2.9C10.6 18.3 5.2 12.4 4 4.4z"/></svg>
          <span class="contact-item__text">+1 (555) 0142 376</span>
        </li>
        <li class="contact-item">
          <svg class="contact-item__icon" viewBox="0 0 24 24" aria-hidden="true"><path d="M7 1h10a1.5 1.5 0 0 1 1.5 1.5v19A1.5 1.5 0 0 1 17 23H7a1.5 1.5 0 0 1-1.5-1.5v-19A1.5 1.5 0 0 1 7 1zm0.5 3v14h9V4zM12 19.3a1 1 0 1 0 0 2 1 1 0 0 0 0-2z"/></svg>
          <span class="contact-item__text">+1 (555) 0198 204</span>
        </li>
        <li class="contact-item">
          <svg class="contact-item__icon" viewBox="0 0 24 24" aria-hidden="true"><path d="M12 1a7.5 7.5 0 0 0-7.5 7.5C4.5 14 12 23 12 23s7.5-9 7.5-14.5A7.5 7.5 0 0 0 12 1z"/></svg>
          <span class="contact-item__text">48 Harbour Lane, Eastmere,<br>NY 10027<br>P.O. Box: 704519</span>
        </li>
        <li class="contact-item contact-item--email">
          <svg class="contact-item__icon" viewBox="0 0 24 24" aria-hidden="true"><path d="M2 5h20v14H2zm1.5 1.5L12 13l8.5-6.5z" fill-rule="evenodd"/></svg>
          <span class="contact-item__text">mail@ardenbay.com</span>
        </li>
      </ul>
    </section>
  </article>
</main>
</body>
</html>
```